Property Services Company Needs a Brochure Design

Looking for a new brochure design for an existing property services company.

We provide a range of property services from, market research, real estate brokerage, valuation and appraisal, property development and other real estate consulting services.

We would like a fresh modern brochure design with good graphics and features. Our colours are white, blue and orange.

The design should communicate, attention to detail, superior service delivery and distinction in results.
Updates

I would like the brochure to be roughly about 20 pages.

Containing the following,

1) An introduction
2) Contents Page
2) What we do
3) Our Services
4) Agency & Brokerage
5) Real Estate Consulting
6) Market Research
7) Appraisal & Valuation
8) Project Management
9) Property Development

I would also like icons to represent items 4,5,6,7,8 & 9, they should be represented vertically on each of the pages from the contents page and highlighted individually on the pages that they represent.. i.e. on appraisal & valuation page, all six icons will be arranged vertically and the appraisal and valuations icon will be highlighted.

I will also like to have images that depict the services on the various pages.

I have some pages I think will flow which I will upload shortly.

Industry/Entity Type

Real Estate

Font styles to use
Serif

Colors
f78f20
0455a3

```html
<!DOCTYPE html>
<html lang="en">
<head>
<meta charset="utf-8">
<title>Calloway Property Services – Brochure Spreads</title>
<link href="https://fonts.googleapis.com/css2?family=Open+Sans:ital,wght@0,400;0,600;0,700;1,400;1,700&family=Oswald:wght@400&display=swap" rel="stylesheet">
<style>
  :root{
    --stage:#1f1f1f;
    --slate:#2c3641;
    --slate-deep:#232a33;
    --navy:#0b3a78;
    --blue:#0455a3;
    --orange:#f78f20;
    --orange-deep:#c06a12;
    --paper:#f2f2f2;
    --paper-shade:#c9c9c9;
    --ink:#111418;
    --ink-soft:#3a3f45;
    --white:#ffffff;
  }
  *{margin:0;padding:0;box-sizing:border-box}
  html,body{width:1200px;height:900px;overflow:hidden}
  body{background:var(--stage);font-family:"Open Sans",Arial,sans-serif;position:relative}
  .spread{position:absolute;left:112px;width:1008px;overflow:hidden;box-shadow:0 4px 14px rgba(0,0,0,.6)}
  .spread--cover{top:88px;height:354px;background:linear-gradient(135deg,#34404d 0%,var(--slate) 55%,var(--slate-deep) 100%)}
  .spread--inner{top:502px;height:355px;background:var(--paper)}
  .shapes{position:absolute;inset:0;width:100%;height:100%}
  .abs{position:absolute}

  /* cover back */
  .brand{color:var(--white);text-align:center}
  .brand__name{font-size:26px;font-weight:400;line-height:1}
  .brand__sub{font-size:8px;margin-top:3px}
  .brand--back{left:170px;top:48px;width:200px}
  .tagline{font-weight:700;font-size:13px;color:var(--white)}
  .tagline--back{left:156px;top:112px}
  .services{left:12px;top:154px;font-family:"Oswald","Arial Narrow",sans-serif;font-size:11.5px;color:var(--orange);letter-spacing:-.2px;white-space:nowrap}
  .contact{font-size:10px;color:#e6e6e6;display:flex;align-items:center;gap:8px;white-space:nowrap}
  .contact svg{width:10px;height:10px;flex:none}

  /* cover front */
  .brand--front{left:784px;top:66px;width:200px;color:var(--ink)}
  .brand--front .brand__name{font-size:36px}
  .brand--front .brand__sub{font-size:11px;color:var(--ink-soft);margin-top:2px}
  .tagline--front{left:794px;top:139px;font-weight:400;color:var(--ink-soft);font-size:12.5px}

  /* inner pages */
  .page-light{position:absolute;left:34px;top:0;width:471px;height:355px;background:radial-gradient(ellipse at 35% 10%,#ffffff 0%,#f1f1f1 45%,var(--paper-shade) 100%)}
  .page-right{position:absolute;left:505px;top:0;width:503px;height:355px;background:linear-gradient(90deg,#d6d6d6 0%,#f4f4f4 55%,#dcdcdc 100%)}
  .commitment{left:70px;top:106px;font-size:19.5px;font-weight:700;font-style:italic;color:var(--ink);line-height:25px}
  .commitment-note{left:70px;top:177px;font-size:15px;font-style:italic;color:var(--ink)}
  .web{left:769px;top:137px;font-size:19px;font-weight:700;font-style:italic;color:var(--orange-deep)}
</style>
</head>
<body>

<!-- Cover: back and front -->
<section class="spread spread--cover">
  <svg class="shapes" viewBox="0 0 1008 354" preserveAspectRatio="none">
    <defs>
      <linearGradient id="paperFront" x1="0" y1="0" x2="1" y2="0">
        <stop offset="0" stop-color="#e9e9e9"/><stop offset=".5" stop-color="#f7f7f7"/><stop offset="1" stop-color="#cfcfcf"/>
      </linearGradient>
      <linearGradient id="blueField" x1="0" y1="0" x2="1" y2="1">
        <stop offset="0" stop-color="#0d4d95"/><stop offset="1" stop-color="#0a2f66"/>
      </linearGradient>
    </defs>
    <polygon points="585,0 1008,0 1008,354 966,354" fill="url(#paperFront)"/>
    <polygon points="633,47 833,237 728,354 328,354" fill="url(#blueField)" role="img" aria-label="Blue hexagon texture panel"/>
    <polygon points="836,242 958,354 730,354" fill="#262d36"/>
    <polygon points="585,0 597,0 976,354 964,354" fill="var(--orange)"/>
  </svg>

  <div class="abs brand brand--back">
    <div class="brand__name">Calloway</div>
    <div class="brand__sub">Property Services</div>
  </div>
  <div class="abs tagline tagline--back">Detail | Delivery| Distinction</div>
  <div class="abs services">Agency &amp; Brokerage, Market Research, Property Development, Real Estate Consulting, Appraisal &amp; Valuation, Project Management</div>

  <div class="abs contact" style="left:20px;top:285px">
    <svg viewBox="0 0 10 10"><path d="M2 1 L4 1 L4.5 3 L3.3 3.8 Q4.3 5.8 6.2 6.7 L7 5.5 L9 6 L9 8 Q5 9 1 4 Q1 2 2 1Z" fill="var(--orange)"/></svg>+234 1 5550147</div>
  <div class="abs contact" style="left:20px;top:305px">
    <svg viewBox="0 0 10 10"><rect x="1" y="4" width="8" height="5" fill="var(--orange)"/><rect x="2" y="1" width="6" height="3" fill="none" stroke="var(--orange)"/></svg>+234 1 5550282</div>
  <div class="abs contact" style="left:20px;top:329px">
    <svg viewBox="0 0 10 10"><path d="M5 0.5 A3 3 0 0 1 8 3.5 Q8 5.5 5 9.5 Q2 5.5 2 3.5 A3 3 0 0 1 5 0.5Z" fill="var(--orange)"/><circle cx="5" cy="3.5" r="1" fill="var(--slate)"/></svg>9th Floor, <b>HARBOUR COURT</b> 48 Marina Road Lagos, Nigeria</div>
  <div class="abs contact" style="left:197px;top:285px">
    <svg viewBox="0 0 10 10"><rect x="0.5" y="2" width="9" height="6" fill="var(--orange)"/><path d="M0.5 2 L5 5.5 L9.5 2" fill="none" stroke="var(--slate)"/></svg>info@calloway.com.ng</div>
  <div class="abs contact" style="left:197px;top:304px">
    <svg viewBox="0 0 10 10"><circle cx="5" cy="5" r="4.5" fill="var(--orange)"/><path d="M0.5 5 H9.5 M5 0.5 V9.5" stroke="var(--slate)" stroke-width=".7"/></svg>www.calloway.com.ng</div>

  <div class="abs brand brand--front">
    <div class="brand__name">Calloway</div>
    <div class="brand__sub">Property Services</div>
  </div>
  <div class="abs tagline tagline--front">Detail | Delivery| Distinction</div>
</section>

<!-- Pages 1–2 -->
<section class="spread spread--inner">
  <div class="page-light"></div>
  <div class="page-right"></div>
  <svg class="shapes" viewBox="0 0 1008 355" preserveAspectRatio="none">
    <defs>
      <linearGradient id="blueInner" x1="0" y1="0" x2="0" y2="1">
        <stop offset="0" stop-color="#0d4d95"/><stop offset="1" stop-color="#0a3470"/>
      </linearGradient>
    </defs>
    <rect x="0" y="0" width="28" height="355" fill="url(#blueInner)" role="img" aria-label="Blue hexagon texture strip"/>
    <rect x="28" y="0" width="6" height="355" fill="var(--orange)"/>
    <polygon points="505,0 543,0 618,76 505,188" fill="url(#blueInner)" role="img" aria-label="Blue hexagon texture panel"/>
    <polygon points="348,355 505,198 505,355" fill="url(#blueInner)" role="img" aria-label="Blue hexagon texture panel"/>
    <polygon points="618,76 783,240 783,355 918,355 783,240 783,131 505,131 505,188" fill="url(#blueInner)"/>
    <polygon points="783,240 918,355 783,355" fill="url(#blueInner)"/>
    <rect x="508" y="131" width="275" height="224" fill="#8a8f96" role="img" aria-label="Photo of an engineer in a hard hat reviewing building plans"/>
    <polygon points="543,0 553,0 928,355 918,355" fill="var(--orange)"/>
    <polygon points="343,355 618,80 624,86 353,355" fill="var(--orange)"/>
  </svg>

  <div class="abs commitment">Our commitment is to provide&nbsp; client<br>satisfaction in everything that we do.</div>
  <div class="abs commitment-note">This is key in maintaining&nbsp; our business relationships</div>
  <div class="abs web">www.calloway.com.ng</div>
</section>

</body>
</html>
```